Vosley Insurance Stationery Design Project

We need a stationery design for business cards, letterhead and envelopes.

Please refer to attached brief for further information.

Industry/Entity Type

Business

```html
<!DOCTYPE html>
<html lang="en">
<head>
<meta charset="utf-8">
<title>Vosley Insurance — Business Card</title>
<link href="https://fonts.googleapis.com/css2?family=Source+Sans+3:wght@400;600;700&display=swap" rel="stylesheet">
<style>
  :root {
    --backdrop: #b88a1f;
    --card-front: #ffffff;
    --card-back: #cfcfcf;
    --orange: #f47321;
    --grey-mark: #bdbdbd;
    --grey-text: #a9a9a9;
    --ink: #2b2b2b;
    --title-grey: #6a6a6a;
  }
  * { box-sizing: border-box; margin: 0; padding: 0; }
  html, body { width: 1200px; height: 686px; overflow: hidden; }
  body {
    background: var(--backdrop);
    font-family: "Source Sans 3", "Myriad Pro", sans-serif;
    position: relative;
  }
  .card {
    position: absolute;
    width: 524px;
    height: 298px;
  }
  .card--front { left: 55px; top: 157px; background: var(--card-front); }
  .card--back  { left: 612px; top: 241px; background: var(--card-back); }

  /* front */
  .brand {
    position: absolute;
    top: 30px; left: 0; right: 0;
    display: flex; justify-content: center; align-items: center; gap: 10px;
  }
  .brand__dot { width: 20px; height: 20px; border-radius: 50%; background: var(--orange); }
  .brand__name {
    font-size: 38px; font-weight: 600; color: var(--grey-mark);
    letter-spacing: 0.5px; line-height: 1;
  }
  .side-bar {
    position: absolute; top: 125px; height: 56px; width: 17px;
    display: flex; gap: 2px;
  }
  .side-bar::before { content: ""; width: 13px; background: var(--orange); }
  .side-bar::after  { content: ""; width: 3px; background: var(--grey-mark); }
  .side-bar--left  { left: 0; }
  .side-bar--right { right: 0; flex-direction: row-reverse; }

  .contact { position: absolute; left: 0; right: 0; text-align: center; }
  .contact__person { top: 112px; font-size: 16.5px; }
  .contact__name { color: var(--orange); font-weight: 700; }
  .contact__sep { color: var(--ink); margin: 0 4px; font-weight: 400; font-size: 13px; }
  .contact__role { color: var(--title-grey); font-weight: 700; font-size: 13px; }
  .contact__address { top: 135px; font-size: 12.6px; color: var(--ink); }
  .contact__lines { top: 156px; font-size: 12.6px; color: var(--ink); word-spacing: 1px; }
  .contact__lines b { color: var(--orange); font-weight: 700; }
  .contact__lines span { margin: 0 7px; }
  .tagline {
    position: absolute; top: 180px; left: 0; right: 0; text-align: center;
    font-size: 12.6px; font-weight: 700; color: var(--grey-text);
  }
  .disclosure {
    position: absolute; top: 204px; left: 20px; right: 20px; text-align: center;
    font-size: 12.4px; line-height: 17px; color: var(--orange);
  }

  /* back */
  .back-dot {
    position: absolute; left: 31px; top: 82px;
    width: 41px; height: 41px; border-radius: 50%; background: var(--orange);
  }
  .back-name {
    position: absolute; left: 82px; top: 92px;
    width: 122px;
    font-size: 25px; font-weight: 700; color: var(--orange); line-height: 1.1;
  }
  .back-rule {
    position: absolute; left: 217px; top: 85px;
    width: 4px; height: 118px; border-radius: 2px; background: var(--orange);
  }
  .back-web {
    position: absolute; left: 243px; top: 131px;
    font-size: 14px; font-weight: 700; color: var(--orange); letter-spacing: 1.6px;
    white-space: nowrap;
  }
</style>
</head>
<body>
  <section class="card card--front">
    <div class="brand">
      <span class="brand__dot"></span>
      <span class="brand__name">Vosley Insurance</span>
    </div>
    <div class="side-bar side-bar--left"></div>
    <div class="side-bar side-bar--right"></div>
    <p class="contact contact__person">
      <span class="contact__name">Mara Holt</span><span class="contact__sep">|</span><span class="contact__role">Director</span>
    </p>
    <p class="contact contact__address">Level 4, 18 Carrow St Northbridge NSW 2063 PO Box 418 Northbridge NSW 2062</p>
    <p class="contact contact__lines">
      <b>T</b> : (02) 8104 2275<span></span><b>F</b> : (02) 9841 3306<span></span><b>M</b> : 0471 529 804<span></span><b>E</b> : mholt@vosley.net.au
    </p>
    <p class="tagline">Business and Life Insurance Brokers and Advisers</p>
    <p class="disclosure">
      Authorised Representative No. 418273<br>
      Harbourline Advisory Pty Limited AFSL 251830 Harbourline<br>
      Financial Services Pty Ltd and its advisers are members of Calder Financial<br>
      Advisers and Authorised Representatives of Westmere Advice Group Pty Ltd AFSL 247615
    </p>
  </section>

  <section class="card card--back">
    <span class="back-dot"></span>
    <span class="back-name">Vosley<br>Insurance</span>
    <span class="back-rule"></span>
    <p class="back-web">www.vosleyinsurance.com.au</p>
  </section>
</body>
</html>
```